brqnal new business card design project

we need a new business card design. you can view info about us @ brqnal-example.com. i have attached an example of our previous card with our previous name that we no longer use. We really liked the design, colors etc. look below to see more info about this project. it asks for a limited number of words. please see our website for more info about our compnay.

Target Market(s)

law enforcement

Contact Information for Business Card

i have uploaded an example of what we used before that we liked.

Font styles to use
Serif

```html
<!DOCTYPE html>
<html lang="en">
<head>
<meta charset="utf-8">
<title>brqnal business card</title>
<link rel="stylesheet" href="https://fonts.googleapis.com/css2?family=Source+Serif+4:opsz,wght@8..60,300;8..60,400;8..60,600&display=swap">
<style>
  :root {
    --backdrop: #b9b9b9;
    --card: #f1f1f1;
    --ink: #1c2226;
    --navy: #0c1a22;
    --blue: #0f6fb0;
    --white: #ffffff;
  }
  * { margin: 0; padding: 0; box-sizing: border-box; }
  html, body { width: 1200px; height: 576px; overflow: hidden; }
  body {
    background: var(--backdrop);
    position: relative;
    font-family: "Source Serif 4", Georgia, serif;
    color: var(--ink);
  }
  .card {
    position: absolute;
    top: 138px;
    width: 484px;
    height: 294px;
    background: var(--card);
    border-radius: 13px;
    overflow: hidden;
  }
  .card--front { left: 82px; }
  .card--back { left: 602px; width: 480px; height: 291px; }

  .wordmark {
    font-weight: 300;
    color: var(--ink);
    line-height: 1;
    white-space: nowrap;
  }
  .card--front .wordmark {
    position: absolute;
    top: 94px;
    left: 0;
    width: 100%;
    text-align: center;
    font-size: 62px;
    letter-spacing: 5px;
  }
  .front-bands { position: absolute; left: 0; top: 0; }
  .front-url {
    position: absolute;
    right: 16px;
    bottom: 11px;
    color: var(--white);
    font-size: 11.5px;
    letter-spacing: 1.6px;
    white-space: nowrap;
  }

  .back-bar { position: absolute; left: 0; top: 0; }
  .card--back .wordmark {
    position: absolute;
    top: 31px;
    left: 62px;
    font-size: 52px;
    letter-spacing: 4px;
  }
  .holder { position: absolute; left: 59px; top: 135px; }
  .holder__name {
    font-weight: 600;
    font-size: 19px;
    line-height: 24px;
    color: var(--blue);
  }
  .holder__title { font-size: 12px; line-height: 16px; margin-top: 2px; }
  .contacts { position: absolute; left: 59px; top: 191px; list-style: none; }
  .contacts li {
    display: flex;
    align-items: center;
    height: 18.5px;
    font-size: 13px;
    white-space: nowrap;
  }
  .contacts svg { width: 11px; height: 11px; margin: 0 14px 0 4px; fill: var(--blue); flex: none; }
  .address { position: absolute; left: 59px; top: 253px; font-size: 13px; white-space: nowrap; }
</style>
</head>
<body>

<section class="card card--front" aria-label="Card front">
  <div class="wordmark">BRQNAL</div>
  <svg class="front-bands" width="484" height="294" viewBox="0 0 484 294" aria-hidden="true">
    <polygon points="0,270 193,270 183,294 0,294" fill="var(--blue)"/>
    <polygon points="202,270 262,270 252,294 192,294" fill="var(--blue)"/>
    <polygon points="282,256 484,256 484,294 266,294" fill="var(--navy)"/>
  </svg>
  <div class="front-url">www.brqnal-example.com</div>
</section>

<section class="card card--back" aria-label="Card back">
  <svg class="back-bar" width="40" height="291" viewBox="0 0 40 291" aria-hidden="true">
    <rect x="0" y="0" width="34" height="291" fill="var(--navy)"/>
    <rect x="36" y="0" width="2.5" height="291" fill="var(--blue)"/>
  </svg>
  <div class="wordmark">BRQNAL</div>
  <div class="holder">
    <div class="holder__name">Daniel Marsh</div>
    <div class="holder__title">Founder/Chief Executive Officer</div>
  </div>
  <ul class="contacts">
    <li>
      <svg viewBox="0 0 12 12" aria-hidden="true"><path d="M1 4c0-1.5 2-2.5 5-2.5S11 2.5 11 4v1H8.5V3.8h-5V5H1z M3 6h6l1.5 4.5h-9z"/></svg>
      800.555.0142
    </li>
    <li>
      <svg viewBox="0 0 12 12" aria-hidden="true"><path d="M0.5 2.5h11v7h-11z M1 3l5 4 5-4" stroke="var(--card)" stroke-width="0.8"/></svg>
      info@brqnal-example.com
    </li>
    <li>
      <svg viewBox="0 0 12 12" aria-hidden="true"><circle cx="6" cy="6" r="5.5"/><path d="M0.5 6h11 M6 0.5v11 M6 0.5c-3 3-3 8 0 11 M6 0.5c3 3 3 8 0 11" stroke="var(--card)" stroke-width="0.7" fill="none"/></svg>
      www.brqnal-example.com
    </li>
  </ul>
  <div class="address">1420 Alder Creek Road Austin, TX 78701</div>
</section>

</body>
</html>
```